IRON PEAK TRAINING- Shooting Range!!!And virtual shooting range!!!

We are looking to do a clean cut web page for shooting range. We have indoor shooting simulator, retail store that sales accessories and pistols, rifles and shot guns. We are membership based for indoor shooting range Only and virtual shooting is open to public as well as retail store. We also specialize in shooting training classes and CWP classes.
Updates

Thank you for your patience. We are working with a busy travel schedule. We will be making final decisions tomorrow and moving forward with getting this launched. Regards, Gerald

Target Market(s)

Public and private entertainment

Industry/Entity Type

Training

Number of Pages Required

5+ page

Font styles to use
Sans Serif

Requirements
Must have
• Clean and easy approach we really like the website our friend has www.valormarkline.com please take a look at a lay out. We would like to also add onli member schedule that is available for shooting sections and that they can access and book them selvs.
Nice to have
• White, black, gray or red colors

```html
<!DOCTYPE html>
<html lang="en">
<head>
<meta charset="utf-8">
<title>Iron Peak Training</title>
<link href="https://fonts.googleapis.com/css2?family=Oswald:wght@500;600&family=Roboto:wght@400;500&family=Open+Sans:wght@400&display=swap" rel="stylesheet">
<style>
:root{
  --red:#e0282e;
  --red-dark:#b81c22;
  --wood:#2a2522;
  --wood-dark:#1a1715;
  --black:#000;
  --band-gray:#4e4e4e;
  --section-dark:#151515;
  --white:#fff;
  --text-light:#d8d8d8;
  --text-dark:#444;
  --silver:#a9a9a9;
}
*{margin:0;padding:0;box-sizing:border-box}
html,body{width:878px;height:1200px;overflow:hidden;background:var(--white)}
body{position:relative;font-family:'Roboto',sans-serif}
.abs{position:absolute}
.wood{background:repeating-linear-gradient(90deg,var(--wood) 0 34px,var(--wood-dark) 34px 36px,#2f2926 36px 70px,var(--wood-dark) 70px 72px)}

.site-header{left:0;top:0;width:878px;height:118px}
.nav a{position:absolute;top:50px;color:var(--white);font-size:12px;text-decoration:none;letter-spacing:.2px}
.nav a.active{top:42px;left:65px;width:57px;height:28px;line-height:28px;text-align:center;background:var(--red);border-radius:2px}
.brand{left:378px;top:30px;width:124px;text-align:center;color:var(--white);font-weight:500;font-size:15px;line-height:19px;letter-spacing:1px}
.brand-mark{display:block;width:26px;height:26px;border-radius:50%;background:var(--white);margin:0 auto 6px}

.hero{left:0;top:118px;width:878px;height:370px;background:radial-gradient(circle at 520px 200px,#4a4a4a 0,#1a1a1a 230px,var(--black) 320px)}
.hero-title{left:78px;top:106px;font-family:'Oswald',sans-serif;font-weight:600;font-size:46px;line-height:1;color:var(--white);letter-spacing:-1px;transform:scaleX(.9);transform-origin:left}
.hero-title span{color:var(--red)}
.hero-sub{left:81px;top:166px;font-family:'Oswald',sans-serif;font-weight:500;font-size:22px;color:var(--white);letter-spacing:-.5px;transform:scaleX(.9);transform-origin:left}
.btn{display:block;background:linear-gradient(var(--red),var(--red-dark));color:var(--white);text-align:center;border-radius:3px;font-weight:500}
.hero-btn{left:78px;top:212px;width:127px;height:39px;line-height:39px;font-size:18px}
.hero-photo{left:378px;top:40px;width:392px;height:290px;
  background:
    linear-gradient(180deg,transparent 0 18%,#c9c9c9 19%,#8e8e8e 30%,#1c1c1c 34%,#0d0d0d 100%);
  -webkit-mask:radial-gradient(ellipse 60% 55% at 55% 45%,#000 55%,transparent 100%);
          mask:radial-gradient(ellipse 60% 55% at 55% 45%,#000 55%,transparent 100%)}
.slider-dots{left:834px;top:140px}
.slider-dots i{display:block;width:7px;height:7px;border-radius:50%;background:var(--white);margin-bottom:6px}
.slider-dots i.on{background:var(--red)}

.welcome{left:0;top:488px;width:878px;height:196px;background:var(--band-gray);text-align:center;color:var(--white)}
.welcome h1{position:absolute;top:36px;width:100%;font-size:18px;font-weight:400}
.welcome p{position:absolute;top:70px;left:90px;width:698px;font-family:'Open Sans',sans-serif;font-size:11px;line-height:19px;color:var(--text-light)}
.welcome .btn{left:388px;top:127px;width:102px;height:30px;line-height:30px;font-size:12px}

.services{left:0;top:684px;width:878px;height:276px;background:var(--section-dark)}
.service{position:absolute;top:35px;width:231px}
.service .photo{width:231px;height:140px;border:2px solid #ddd}
.service h2{margin-top:14px;text-align:center;color:var(--white);font-size:14px;font-weight:500}
.service p{margin-top:11px;text-align:center;color:var(--text-light);font-size:10px;line-height:16px;letter-spacing:.3px}

.bookings{left:0;top:960px;width:878px;height:168px;background:var(--white)}
.book-photo{left:81px;top:35px;width:124px;height:95px;border-radius:3px;background:linear-gradient(135deg,#3a3a3a,#0d0d0d)}
.book-title{left:221px;top:38px;color:var(--red);font-size:14px}
.book-text{left:221px;top:61px;width:292px;color:var(--text-dark);font-size:11.5px;line-height:18px}
.book-btn{left:223px;top:105px;width:74px;height:23px;line-height:23px;font-size:11px;border-radius:2px;font-weight:400}
.signup{left:554px;top:23px;width:256px;height:114px;border:1px solid #cfcfcf;padding:5px;
  background:#f6f6f6 repeating-linear-gradient(0deg,transparent 0 7px,#ececec 7px 8px),repeating-linear-gradient(90deg,transparent 0 7px,#ececec 7px 8px)}
.signup h3{margin:8px 0 0 11px;font-family:'Open Sans',sans-serif;font-weight:400;font-size:15px;color:#333}
.signup .field{position:absolute;left:17px;top:40px;width:220px;height:29px;border:1px solid #bbb;background:linear-gradient(#e6e6e6,#fafafa);font-size:11px;color:#555;line-height:27px;padding-left:11px}
.signup .btn{position:absolute;left:178px;top:76px;width:61px;height:24px;line-height:24px;font-size:12px;border-radius:4px}

.site-footer{left:0;top:1128px;width:878px;height:72px;border-top:2px solid #000}
.copyright{left:78px;top:30px;color:var(--white);font-size:12px}
.social{top:20px;width:32px;height:32px;border:1px solid #cfcfcf;border-radius:50%;display:flex;align-items:center;justify-content:center}
.social svg{width:16px;height:16px;fill:none;stroke:var(--white);stroke-width:1.6;stroke-linecap:round;stroke-linejoin:round}
</style>
</head>
<body>
<header class="site-header abs wood">
  <nav class="nav">
    <a class="active" href="#">HOME</a>
    <a href="#" style="left:137px">ABOUT US</a>
    <a href="#" style="left:222px">SERVICE</a>
    <a href="#" style="left:298px">TRAINING</a>
    <a href="#" style="left:496px">CLASSES</a>
    <a href="#" style="left:584px">ACCESSORIES</a>
    <a href="#" style="left:699px">BLOG</a>
    <a href="#" style="left:763px">CONTACTS</a>
  </nav>
  <div class="brand abs"><span class="brand-mark"></span>IRON PEAK<br>TRAINING</div>
</header>

<section class="hero abs">
  <div class="hero-photo abs" role="img" aria-label="Semi-automatic pistol with silver slide and black frame"></div>
  <div class="hero-title abs">CWP <span>CLASSES</span></div>
  <div class="hero-sub abs">SPECIALISE IN SHOOTING TRAINING CLASSES</div>
  <a class="btn hero-btn abs">GET MORE</a>
  <div class="slider-dots abs"><i></i><i class="on"></i><i></i><i></i><i></i></div>
</section>

<section class="welcome abs">
  <h1>WELCOME TO IRON PEAK</h1>
  <p>Lorem Ipsum has been the industry's standard dummy text ever since the 1500s, when an unknown printer took a galley of type and scrambled it to make a type specimen book. It has survived not only five centuries, but also the leap into electronic typesetting</p>
  <a class="btn abs">READ MORE</a>
</section>

<section class="services abs">
  <div class="service" style="left:78px">
    <div class="photo" role="img" aria-label="Trainee aiming a rifle down an indoor range" style="background:linear-gradient(90deg,#4b5a3a,#2a2a2a 60%,#5a5a4a)"></div>
    <h2>TRAINING CLASSES</h2>
    <p>Lorem ipum dolor sit amet consect etuer adip isccing elint vestibulum estie lacuean nonumm</p>
  </div>
  <div class="service" style="left:326px">
    <div class="photo" role="img" aria-label="Two tactical shooters practising in a range lane" style="background:linear-gradient(#6a6f78,#1e2026)"></div>
    <h2>CWP CLASSES</h2>
    <p>Lorem ipum dolor sit amet consect etuer adip isccing elint vestibulum estie lacuean nonumm</p>
  </div>
  <div class="service" style="left:574px">
    <div class="photo" role="img" aria-label="Wall rack of rifles and shotguns" style="background:linear-gradient(#8f8a82,#3b3936)"></div>
    <h2>INDOOR SHOOTING RANGE</h2>
    <p>Lorem ipum dolor sit amet consect etuer adip isccing elint vestibulum estie lacuean nonumm</p>
  </div>
</section>

<section class="bookings abs">
  <div class="book-photo abs" role="img" aria-label="Range lobby interior"></div>
  <div class="book-title abs">ONLINE MEMBER BOOKINGS</div>
  <div class="book-text abs">Lorem Ipsum has been the industry's standard dummy text ever since the 1500s</div>
  <a class="btn book-btn abs">BOOKING</a>
  <form class="signup abs">
    <h3>Email sign up</h3>
    <div class="field">Enter Your Email Address</div>
    <a class="btn">Sign Up</a>
  </form>
</section>

<footer class="site-footer abs wood">
  <div class="copyright abs">Copyright © 2015 &nbsp;|&nbsp; Privacy policy</div>
  <span class="social abs" style="left:661px" aria-label="Email"><svg viewBox="0 0 16 16"><rect x="2" y="4" width="12" height="9" rx="1"/><path d="M2 5l6 4 6-4"/></svg></span>
  <span class="social abs" style="left:698px" aria-label="Phone"><svg viewBox="0 0 16 16"><path d="M4 2l2.5 3-1.5 1.5c.8 1.8 2.2 3.2 4 4L10.5 9 13.5 11.5 12 14C7 13.5 2.5 9 2 4z"/></svg></span>
  <span class="social abs" style="left:735px" aria-label="Location"><svg viewBox="0 0 16 16"><path d="M8 14s-4.5-4.5-4.5-8a4.5 4.5 0 019 0c0 3.5-4.5 8-4.5 8z"/><circle cx="8" cy="6" r="1.6"/></svg></span>
  <span class="social abs" style="left:773px" aria-label="Website"><svg viewBox="0 0 16 16"><circle cx="8" cy="8" r="6"/><path d="M2 8h12M8 2c2 2 2 10 0 12M8 2c-2 2-2 10 0 12"/></svg></span>
</footer>
</body>
</html>
```